Web Design job - Condo Debts Collection Business needs a Web Design

I need a site for a client, who works with condo debts collection, and ensure all revenues provided by condo fees will be always available to the building manager of condo on a specific date, regardless of defaults.
I have the visual identity (logo, slogan and colors) of the company, and some requirements on layout (kind of slider, menu options, phone number on a noble position, etc) - maybe I can do a sketch, but I like the idea of give some freedom to designer.

*** PLEASE, we have no interest in templates. We want something new***

Target Market(s)

I have two targets for this design: - Condominium's building manager. This target is looking for a solution to overdue debts on it's condo. - Residents on condominiums. This target wants to live in a better place, where their neighbors pay their condominium fees on time.

Number of Pages Required

1 page

Requirements
Must have
• - Slider with title, some short text related, a nice image (I prefer happy and/or peaceful family, people doing business, happy friends, and so on).
• - I have a special attention to menu. I'm looking for one I can have a nice effect, more elegant, charming, kind of innovative.
• - Phone number on the top (or clearly visible).
• - Member log in area or icon on the top (or clearly visible).
• - News/articles area.
• - Modern fonts, with good quality, sans-serif on areas where reading is more intensive (prefer Google web-fonts).
• - Colors specified on attached files.
Nice to have
• - Clear background color, cause it's better to read larger texts (like articles). Dark backgrounds makes reading difficult.
• - A site with effects (like shadows, lines, curves, gradients, lights) is usually pretty.
• - I pay attention on beautiful footers.
Should not have
• - Images with a lot of money (I don't sell richness, I sell tranquility, peace, harmony, safety).
• - Poor menu.

```html
<!DOCTYPE html>
<html lang="en">
<head>
<meta charset="utf-8">
<title>Velora – Condo Fee Guarantee</title>
<link href="https://fonts.googleapis.com/css2?family=Raleway:wght@300;400;500;700&family=Roboto+Slab:wght@300;400;700&family=Roboto:wght@400;500;700&display=swap" rel="stylesheet">
<style>
:root{
  --gold:#e2ab1e;
  --gold-dark:#c9940f;
  --ink:#2e2e2e;
  --muted:#555;
  --line:#dcdcdc;
  --band:#ededed;
  --white:#fff;
  --footer:#f4f5f9;
}
*{box-sizing:border-box;margin:0;padding:0}
html,body{width:1200px;height:3629px;overflow:hidden}
body{position:relative;background:var(--white);color:var(--ink);font-family:"Roboto Slab",serif}
.abs{position:absolute}
a{color:inherit;text-decoration:none}

/* header */
.site-header{position:absolute;left:0;top:0;width:1200px;height:114px;background:var(--white);z-index:3}
.brand{position:absolute;left:160px;top:28px;display:flex;align-items:center;gap:12px}
.brand-mark{width:44px;height:44px;background:var(--gold)}
.brand-name{font-family:"Raleway",sans-serif;font-weight:700;font-size:40px;color:var(--ink);letter-spacing:.5px}
.top-tab{position:absolute;right:160px;top:0;width:330px;height:32px;background:var(--gold);border-radius:0 0 0 22px;display:flex;align-items:center;justify-content:space-around;font-family:"Roboto",sans-serif;font-size:11px;color:var(--white);letter-spacing:.3px}
.top-tab span{display:flex;align-items:center;gap:6px}
.main-nav{position:absolute;left:418px;top:68px;display:flex;gap:0;font-family:"Roboto Slab",serif;font-size:14px}
.main-nav a{padding:6px 20px;border-radius:14px}
.main-nav a.active{background:var(--gold);color:var(--ink);font-weight:700}
.main-nav .caret{color:var(--gold);font-size:10px}

/* hero */
.hero{position:absolute;left:0;top:114px;width:1200px;height:596px;clip-path:polygon(0 0,100% 0,100% 84%,0 100%);
  background:linear-gradient(100deg,#6c5a4a 0%,#a58e76 35%,#8c8075 60%,#6d6d6f 100%)}
.hero-photo{position:absolute;inset:0}
.hero-accent{position:absolute;right:0;top:0;width:540px;height:100%;background:linear-gradient(115deg,rgba(226,171,30,0) 0%,rgba(226,171,30,.55) 45%,rgba(226,171,30,.8) 100%)}
.hero-title{position:absolute;left:160px;top:200px;font-family:"Raleway",sans-serif;font-weight:300;font-size:44px;color:var(--white)}
.hero-text{position:absolute;left:160px;top:258px;width:420px;font-size:20px;line-height:30px;color:var(--white)}
.slider-dots{position:absolute;left:568px;top:516px;display:flex;gap:6px}
.slider-dots i{width:11px;height:11px;border-radius:50%;background:var(--white)}
.slider-dots i.on{background:var(--gold)}

/* about */
.about-photo{left:160px;top:765px;width:475px;height:328px;border:4px solid var(--gold);background:linear-gradient(135deg,#d8d4cd,#8d7d6c 55%,#4c4a4e)}
.section-title{font-family:"Raleway",sans-serif;font-weight:300;color:var(--ink)}
.about-title{left:675px;top:778px;font-size:44px}
.body-small{font-size:10.5px;line-height:19px;color:var(--muted)}
.about-text{left:680px;top:846px;width:355px}
.btn{display:inline-block;font-family:"Roboto",sans-serif;font-weight:700;font-size:9px;letter-spacing:.5px;text-transform:uppercase;border-radius:16px;text-align:center;line-height:28px;height:30px;width:104px;border:1.5px solid var(--gold);color:var(--gold-dark);background:var(--white)}
.btn.solid{background:var(--gold);color:var(--white)}
.about-btn{left:678px;top:1038px}

/* what we do */
.services-band{left:0;top:1130px;width:1200px;height:660px;background:var(--band);clip-path:polygon(0 12%,100% 0,100% 92%,0 100%)}
.services-title{left:0;top:1258px;width:1200px;text-align:center;font-size:44px}
.service-card{top:1355px;width:208px;height:295px;background:var(--white);border:1px solid var(--line);text-align:center;padding-top:38px}
.service-card.featured{border-bottom:4px solid var(--gold)}
.service-card svg{width:72px;height:72px}
.service-card h3{font-family:"Raleway",sans-serif;font-weight:500;font-size:15px;margin:14px 0 10px;letter-spacing:.5px}
.service-card p{font-size:10px;line-height:17px;color:var(--muted);padding:0 20px;height:56px}
.service-card .btn{margin-top:14px}

/* news */
.news-title{left:0;top:1822px;width:1200px;text-align:center;font-size:44px}
.news-item{width:275px}
.news-photo{height:164px;clip-path:polygon(0 0,100% 0,100% 100%,18% 100%,13% 92%,8% 100%,0 100%)}
.news-meta{font-family:"Roboto",sans-serif;font-weight:700;font-size:9.5px;color:var(--gold-dark);margin-top:14px;display:flex;gap:28px}
.news-item h3{font-family:"Raleway",sans-serif;font-weight:500;font-size:19px;margin:8px 0 10px}
.news-item p{font-size:10px;line-height:17px;color:var(--muted);height:58px}
.news-item .btn{margin-top:8px}

/* contact */
.contact-band{left:0;top:2765px;width:1200px;height:535px;background:linear-gradient(90deg,#eeeeee,#f4f4f4);clip-path:polygon(0 0,100% 5%,100% 100%,0 100%)}
.contact-title{left:160px;top:2875px;font-size:44px}
.contact-intro{left:162px;top:2950px;width:470px}
.contact-line{left:160px;display:flex;align-items:flex-start;gap:22px;font-size:12.5px;line-height:21px;color:var(--muted)}
.contact-line svg{width:20px;height:20px;flex:none;margin-top:2px}
.contact-form{left:719px;top:2805px;width:318px;height:412px;background:var(--white);border:5px solid var(--gold);box-shadow:0 6px 18px rgba(0,0,0,.18);padding:20px 22px}
.contact-form h2{font-family:"Raleway",sans-serif;font-weight:400;font-size:26px;text-align:center;margin-bottom:16px}
.field{height:28px;border:1px solid var(--line);border-radius:3px;margin-bottom:8px;display:flex;align-items:center;gap:8px;padding-left:8px;font-size:10px;color:#777}
.field i{width:14px;height:14px;border-radius:50%;border:1px solid #bbb}
.field.tall{height:100px;align-items:flex-start;padding-top:7px}
.send{height:30px;background:linear-gradient(#e8b62c,var(--gold-dark));color:var(--white);font-family:"Roboto",sans-serif;font-weight:700;font-size:12px;text-align:center;line-height:30px;margin-top:12px}

/* footer */
.site-footer{left:0;top:3290px;width:1200px;height:339px;background:linear-gradient(180deg,var(--white) 0%,var(--footer) 100%)}
.footer-wave{position:absolute;left:0;bottom:0;width:1200px;height:200px}
.footer-brand{left:160px;top:3368px;display:flex;align-items:center;gap:10px}
.footer-brand .brand-mark{width:36px;height:36px}
.footer-brand .brand-name{font-size:32px}
.footer-blurb{left:162px;top:3425px;width:225px}
.footer-col{top:3358px;font-size:10px;line-height:26px;color:var(--muted)}
.footer-col h4{font-family:"Raleway",sans-serif;font-weight:400;font-size:17px;color:var(--ink);margin-bottom:10px;line-height:22px}
.social{display:flex;gap:14px;align-items:center;margin-bottom:20px}
.social i{width:20px;height:20px;border-radius:50%;background:var(--ink)}
.copyright{left:0;top:3580px;width:1200px;text-align:center;font-size:10.5px;color:var(--muted)}
</style>
</head>
<body>

<header class="site-header">
  <div class="brand"><span class="brand-mark"></span><span class="brand-name">velora</span></div>
  <div class="top-tab">
    <span><svg width="11" height="11" viewBox="0 0 12 12"><circle cx="6" cy="3.5" r="2.7" fill="#fff"/><path d="M1 12c0-3 2.2-5 5-5s5 2 5 5z" fill="#fff"/></svg>MEMBER LOG IN</span>
    <span><svg width="11" height="11" viewBox="0 0 12 12"><path d="M2.5 1l2 2.5-1.2 1.3a7 7 0 0 0 3.9 3.9l1.3-1.2 2.5 2-1.3 1.5C5 11 1 7 1 2.3z" fill="#fff"/></svg>Phone: (55) 410 2.7 30</span>
  </div>
  <nav class="main-nav">
    <a class="active" href="#">Home</a>
    <a href="#">About</a>
    <a href="#">Services <span class="caret">▾</span></a>
    <a href="#">Why Choose us?</a>
    <a href="#">Faq</a>
    <a href="#">Contact Us</a>
  </nav>
</header>

<section class="hero">
  <div class="hero-photo" role="img" aria-label="Photo of a happy family relaxing together on a sofa at home"></div>
  <div class="hero-accent"></div>
  <h1 class="hero-title">Welcome to Velora</h1>
  <p class="hero-text">Sed ut perspiciatis unde omniste natus error sit volupiat istarspis und.</p>
  <div class="slider-dots"><i></i><i></i><i></i><i class="on"></i></div>
</section>

<div class="abs about-photo" role="img" aria-label="Photo of a couple meeting a consultant at a table"></div>
<h2 class="abs section-title about-title">About Company</h2>
<p class="abs body-small about-text">We keep condominium budgets steady by paying every monthly fee to the building manager on the agreed date, whether residents pay on time or not. Our team handles the reminders, negotiation and collection work, so managers can plan repairs and services with confidence and residents enjoy a calm, well kept home where every neighbour shares the costs fairly and openly.</p>
<a class="abs btn solid about-btn" href="#">Read more</a>

<div class="abs services-band"></div>
<h2 class="abs section-title services-title">What We Do</h2>

<div class="abs service-card featured" style="left:160px">
  <svg viewBox="0 0 72 72" fill="none" stroke="#e2ab1e" stroke-width="2"><path d="M8 34L36 12l28 22"/><path d="M14 30v30h44V30"/><rect x="20" y="40" width="12" height="20"/><rect x="38" y="40" width="12" height="10"/><path d="M48 16v8"/></svg>
  <h3>SERSPICIATND</h3>
  <p>Guaranteed monthly revenue delivered on the same date, every month.</p>
  <a class="btn solid" href="#">Read more</a>
</div>
<div class="abs service-card" style="left:383px">
  <svg viewBox="0 0 72 72" fill="none" stroke="#e2ab1e" stroke-width="2"><rect x="10" y="22" width="52" height="34" rx="4"/><path d="M14 22l34-10 4 10"/><rect x="44" y="32" width="18" height="14" rx="2"/><circle cx="51" cy="39" r="2"/></svg>
  <h3>SERSPICIATND</h3>
  <p>Careful handling of overdue fees with respectful resident contact.</p>
  <a class="btn" href="#">Read more</a>
</div>
<div class="abs service-card" style="left:607px">
  <svg viewBox="0 0 72 72" fill="none" stroke="#e2ab1e" stroke-width="2"><path d="M14 30L36 12l22 18"/><path d="M20 26v30h32V26"/><circle cx="36" cy="38" r="6"/><path d="M26 56c0-6 4-10 10-10s10 4 10 10"/></svg>
  <h3>SERSPICIATND</h3>
  <p>Clear monthly reports for managers and every resident board.</p>
  <a class="btn" href="#">Read more</a>
</div>
<div class="abs service-card" style="left:830px">
  <svg viewBox="0 0 72 72" fill="none" stroke="#e2ab1e" stroke-width="2"><path d="M20 28L36 14l16 14"/><path d="M24 25v15h24V25"/><path d="M8 52h14l10 6h18l12-10-4-3-12 6H34"/><path d="M22 48h16"/></svg>
  <h3>SERSPICIATND</h3>
  <p>Legal support for difficult cases so the building stays protected.</p>
  <a class="btn" href="#">Read more</a>
</div>

<h2 class="abs section-title news-title">News/Articles</h2>

<article class="abs news-item" style="left:160px;top:1933px">
  <div class="news-photo" role="img" aria-label="Photo of a manager shaking hands with clients in a bright apartment" style="background:linear-gradient(135deg,#cfd8de,#7e8a94)"></div>
  <div class="news-meta"><span>JULY 10, 2018</span><span>0 COMMENTS</span></div>
  <h3>Sed ut perspiciatis mnis is</h3>
  <p>Practical advice for managers on keeping fees current and neighbours informed all year.</p>
  <a class="btn solid" href="#">Read more</a>
</article>
<article class="abs news-item" style="left:463px;top:1933px">
  <div class="news-photo" role="img" aria-label="Photo of a business meeting around an office table" style="background:linear-gradient(135deg,#e2e4e6,#8d939a)"></div>
  <div class="news-meta"><span>JULY 10, 2018</span><span>0 COMMENTS</span></div>
  <h3>Accumsan massa</h3>
  <p>How a guaranteed income helps buildings plan maintenance without surprise extra charges.</p>
  <a class="btn" href="#">Read more</a>
</article>
<article class="abs news-item" style="left:765px;top:1933px">
  <div class="news-photo" role="img" aria-label="Photo of a brick apartment building under a blue sky" style="background:linear-gradient(180deg,#5d8fd0,#a2684d)"></div>
  <div class="news-meta"><span>JULY 10, 2018</span><span>0 COMMENTS</span></div>
  <h3>Sed ut perspiciatisnis is</h3>
  <p>Simple steps residents can take to support a fair and peaceful condominium community.</p>
  <a class="btn" href="#">Read more</a>
</article>
<article class="abs news-item" style="left:160px;top:2323px">
  <div class="news-photo" role="img" aria-label="Photo of colleagues reviewing papers around a wooden table" style="background:linear-gradient(135deg,#3d3d40,#9a7a52)"></div>
  <div class="news-meta"><span>JULY 10, 2018</span><span>0 COMMENTS</span></div>
  <h3>Sed ut perspiciatis mnis is</h3>
  <p>What changes when late payments stop affecting the monthly budget of your building.</p>
  <a class="btn" href="#">Read more</a>
</article>
<article class="abs news-item" style="left:463px;top:2323px">
  <div class="news-photo" role="img" aria-label="Photo of a modern residential tower with balconies" style="background:linear-gradient(180deg,#c9d2da,#6c6e72)"></div>
  <div class="news-meta"><span>JULY 10, 2018</span><span>0 COMMENTS</span></div>
  <h3>Accumsan massa</h3>
  <p>Questions to ask before choosing a collection partner for your residential complex today.</p>
  <a class="btn" href="#">Read more</a>
</article>
<article class="abs news-item" style="left:765px;top:2323px">
  <div class="news-photo" role="img" aria-label="Photo of an older couple reviewing documents with an advisor" style="background:linear-gradient(135deg,#dad7d2,#3f5570)"></div>
  <div class="news-meta"><span>JULY 10, 2018</span><span>0 COMMENTS</span></div>
  <h3>Sed ut perspiciatisnis is</h3>
  <p>Stories from managers who now close every month with a balanced and steady account.</p>
  <a class="btn" href="#">Read more</a>
</article>

<div class="abs contact-band"></div>
<h2 class="abs section-title contact-title">Contact Us</h2>
<p class="abs body-small contact-intro">Talk to our team about guaranteed condo revenue and a simpler collection routine for your building and residents.</p>
<div class="abs contact-line" style="top:3020px">
  <svg viewBox="0 0 20 20" fill="none" stroke="#e2ab1e" stroke-width="1.6"><path d="M10 19s6-6.5 6-11a6 6 0 0 0-12 0c0 4.5 6 11 6 11z"/><circle cx="10" cy="8" r="2.2"/></svg>
  <span>Rua das Acácias, 820 Sala 304, Ed. Horizonte,<br>CEP: 40.210-300, Jardim Alto, Porto Claro-BA</span>
</div>
<div class="abs contact-line" style="top:3107px">
  <svg viewBox="0 0 20 20" fill="none" stroke="#e2ab1e" stroke-width="1.6"><path d="M4 2l3 4-2 2a11 11 0 0 0 7 7l2-2 4 3-2 3C8 19 1 12 1 4z"/></svg>
  <span>Phone: (55) 410 2.7 30</span>
</div>
<div class="abs contact-line" style="top:3162px">
  <svg viewBox="0 0 20 20" fill="none" stroke="#e2ab1e" stroke-width="1.6"><rect x="1.5" y="4" width="17" height="12"/><path d="M1.5 4l8.5 7 8.5-7"/></svg>
  <span>contato@velora.com.br</span>
</div>

<form class="abs contact-form">
  <h2>Contact Form</h2>
  <div class="field"><i></i>Name</div>
  <div class="field"><i></i>Email</div>
  <div class="field"><i></i>Phone</div>
  <div class="field"><i></i>Company</div>
  <div class="field tall"><i></i>Subject</div>
  <div class="send">SEND</div>
</form>

<footer class="abs site-footer">
  <svg class="footer-wave" viewBox="0 0 1200 200" preserveAspectRatio="none"><path d="M0 120 C250 60 450 170 700 110 S1050 60 1200 100 V200 H0z" fill="#e9ebf3"/><path d="M0 160 C300 120 500 190 800 150 S1100 130 1200 150 V200 H0z" fill="#e2e5ee"/></svg>
</footer>
<div class="abs footer-brand"><span class="brand-mark"></span><span class="brand-name">velora</span></div>
<p class="abs body-small footer-blurb">Condo fee collection with guaranteed monthly revenue for managers and peace of mind for residents.</p>
<div class="abs footer-col" style="left:495px">
  <h4>Links</h4>
  Our services<br>How it works<br>Guarantee plans<br>Managers area<br>Residents area
</div>
<div class="abs footer-col" style="left:708px">
  <h4>Connect</h4>
  <div class="social">
    <svg width="22" height="16" viewBox="0 0 22 16"><rect width="22" height="16" fill="#2e2e2e"/><path d="M0 0l11 9 11-9" fill="none" stroke="#fff" stroke-width="1.5"/></svg>
    <i></i><i></i><i></i>
  </div>
  <h4>Policies</h4>
  Privacy<br>Complaint and Feedback
</div>
<div class="abs footer-col" style="left:926px">
  <h4>Other Links</h4>
  Latest news<br>Frequent questions<br>Work with us<br>Partner buildings<br>Member log in
</div>
<p class="abs copyright">© 2018 Velora. All Rights are Reserved. Privacy Policy | Terms of Use | Contact</p>

</body>
</html>
```